International Petrochemical business needs a web design for Clearway Desk system

We need a web design for a "Clearway Desk" system for an international petrochemical company. The web site is used internally within the company. It is hosted by an internal department which provides government permit request service for other departments.

We would like to see designs of two pages using color light blue. (home page, internal page as attached).
Home Page:
1. Header has a background image and small animation. Header on home page can be taller than the header of the internal page.
2. Layout as attached.

Internal Page:
1. Header can use the same background image as the home page and can be shorter to utilize the page for content.
2. The blue icon behind every captions represent an icon. When user move mouse over this icon, it displays the caption in Thai language as a tooltip. This icon needs to be redesign.

The final design should communicate the followings:
- Excellent service provided system in terms of time and accurary
- Rapid growth of business via building petrochemical refinery plant
Updates

For Internal Page, the blue circle behind every captions represent an icon. When mouse over this icon, a tool tip showing the caption in Thai language is shown. Please also design this icon..

There are more feedbacks from customer as followed:

1. Banner should consists of 
    1.1 "Approved" stamp on paper
    1.2 An image of Garuda. It is used on every government documents in Thailand
    1.3 Image of petrochemical plant
2. Each menu item (Home, Permit, Search, etc) should have different colors. Drop down menu will use the same color as its parent menu item.
3. Overall tone of the web page should be light blue with background of the body the web page in white
4. "New Request" button should use green color with icon on it
5. Table header of each box in the body of the page should use dark blue background with text in white

Please kindly submit your revisions.
Thank you.

Industry/Entity Type

Business

Requirements
Must have
• 1. Design for 1024x768 screen resolution
2. Use light blue theme
3. Background of header where the company logo is must have white background

```html
<!DOCTYPE html>
<html lang="en">
<head>
<meta charset="utf-8">
<title>Clearway Desk</title>
<link href="https://fonts.googleapis.com/css2?family=Arimo:wght@400;700&family=Oswald:wght@400&display=swap" rel="stylesheet">
<style>
  :root {
    --sky: #19ade9;
    --violet: #5b5fce;
    --slate: #8e979f;
    --teal: #1aa3c2;
    --lime: #74c52d;
    --lime-dark: #4fa817;
    --navy: #1c1464;
    --head-row: #a9dcee;
    --data-row: #cbe6f0;
    --pager: #e4e4e4;
    --pager-icon: #7f97b3;
    --link: #1a86c8;
    --text: #222;
    --brand-text: #1a4fa0;
    --footer-text: #555;
    --footer-muted: #aaa;
    --alert-red: #e02a1f;
    --alert-amber: #f2a916;
    --white: #fff;
  }
  * { box-sizing: border-box; }
  html, body {
    margin: 0; width: 1200px; height: 1155px; overflow: hidden;
    background: var(--white); font-family: "Arimo", Arial, sans-serif; color: var(--text);
  }
  .page { position: relative; width: 1200px; height: 1155px; }

  .masthead-art {
    position: absolute; left: 0; top: 0; width: 1200px; height: 340px;
    background:
      linear-gradient(180deg, rgba(255,255,255,0) 0%, rgba(255,255,255,0) 70%, var(--white) 100%),
      radial-gradient(ellipse at 75% 45%, #bfe9fb 0%, rgba(191,233,251,0) 55%),
      linear-gradient(90deg, #2a9fe0 0%, #5cc3f2 45%, #8fd9f8 75%, #40b0ea 100%);
  }
  .brand {
    position: absolute; left: 29px; top: 196px;
    display: flex; align-items: center; gap: 8px;
    font-weight: 700; font-size: 17px; color: var(--brand-text);
  }
  .brand-dot { width: 30px; height: 30px; border-radius: 50%; background: var(--alert-red); }
  .app-title {
    position: absolute; left: 245px; top: 180px; margin: 0;
    font-family: "Oswald", sans-serif; font-weight: 400; font-size: 52px; line-height: 1;
    color: var(--navy);
  }

  .main-nav { position: absolute; left: 18px; top: 255px; display: flex; height: 47px; }
  .main-nav a {
    display: flex; align-items: center; justify-content: center;
    font-family: "Oswald", sans-serif; font-weight: 400; font-size: 23px;
    color: var(--white); text-decoration: none; text-transform: uppercase;
  }
  .nav-home { width: 179px; background: var(--sky); }
  .nav-permits { width: 211px; background: var(--violet); }
  .nav-search { width: 179px; background: var(--slate); }
  .nav-reports { width: 238px; background: var(--teal); }
  .nav-admin { width: 174px; background: var(--lime); }
  .nav-help { width: 181px; background: var(--sky); }

  .panel { position: absolute; background: var(--white); }
  .panel-title {
    height: 43px; background: var(--navy); color: var(--white);
    font-size: 17px; padding-left: 10px; display: flex; align-items: center; margin: 0; font-weight: 400;
  }
  .panel table { width: 100%; border-collapse: collapse; table-layout: fixed; font-size: 15px; }
  .panel th {
    height: 28px; background: var(--head-row); color: #1c3e6a; font-weight: 400; text-align: left; padding: 0 0 0 10px;
  }
  .panel td {
    height: 29px; background: var(--data-row); padding: 0 0 0 10px; border-top: 1px solid var(--white);
  }
  .panel td a { color: var(--link); }
  .pager {
    height: 34px; background: var(--pager); border-top: 1px solid var(--white);
    display: flex; align-items: center; gap: 9px; padding-left: 12px;
  }
  .pager svg { display: block; }
  .page-no {
    width: 25px; height: 19px; border: 1px solid #9aa; border-radius: 4px; background: var(--white);
    font-size: 13px; display: flex; align-items: center; justify-content: center;
  }
  .dot { display: inline-block; width: 12px; height: 12px; border-radius: 50%; margin-left: 6px; vertical-align: -1px; }
  .dot-red { background: var(--alert-red); }
  .dot-amber { background: var(--alert-amber); }

  .panel-new { left: 18px; top: 359px; width: 578px; }
  .panel-working { left: 602px; top: 359px; width: 577px; }
  .panel-expiring { left: 18px; top: 604px; width: 1161px; }
  .panel-progress { left: 18px; top: 787px; width: 578px; }
  .panel-recent { left: 602px; top: 846px; width: 577px; }

  .cta-band {
    position: absolute; left: 602px; top: 787px; width: 577px; height: 54px; background: var(--lime);
  }
  .cta-button {
    position: absolute; left: 200px; top: 6px; width: 200px; height: 44px;
    background: var(--lime-dark); border-radius: 4px; color: var(--white); text-decoration: none;
    font-family: "Oswald", sans-serif; font-size: 26px; display: flex; align-items: center; justify-content: center;
  }

  .site-footer {
    position: absolute; left: 18px; top: 1082px; width: 1161px; border-top: 1px solid #d0d0d0;
    display: flex; justify-content: space-between; padding-top: 16px;
  }
  .footer-links { font-size: 13.5px; color: var(--footer-text); }
  .footer-links a { color: var(--footer-text); text-decoration: none; }
  .footer-links span { margin: 0 6px; }
  .copyright { font-size: 14.5px; color: var(--footer-muted); margin-top: -4px; }
</style>
</head>
<body>
<div class="page">
  <div class="masthead-art" role="img" aria-label="Petrochemical plant with pipes and tanks in light blue tones"></div>
  <div class="brand"><span class="brand-dot"></span>Northbay Petrochem</div>
  <h1 class="app-title">Clearway Desk</h1>

  <nav class="main-nav">
    <a class="nav-home" href="#">Home</a>
    <a class="nav-permits" href="#">Permits</a>
    <a class="nav-search" href="#">Search</a>
    <a class="nav-reports" href="#">Reports</a>
    <a class="nav-admin" href="#">Admin</a>
    <a class="nav-help" href="#">Help</a>
  </nav>

  <section class="panel panel-new">
    <h2 class="panel-title">New Requests</h2>
    <table>
      <colgroup><col style="width:164px"><col style="width:187px"><col></colgroup>
      <tr><th>Request No.</th><th>Requested Date</th><th>Branch</th></tr>
      <tr><td><a href="#">56-0003</a></td><td>21/04/2013</td><td>GC1</td></tr>
      <tr><td><a href="#">56-0004</a></td><td>21/04/2013</td><td>GC2</td></tr>
      <tr><td></td><td></td><td></td></tr>
      <tr><td></td><td></td><td></td></tr>
    </table>
    <div class="pager">
      <svg width="12" height="12" viewBox="0 0 12 12"><rect x="1" y="1" width="2" height="10" fill="#7f97b3"/><path d="M11 1 4 6l7 5z" fill="#7f97b3"/></svg>
      <svg width="10" height="12" viewBox="0 0 10 12"><path d="M9 1 2 6l7 5z" fill="#7f97b3"/></svg>
      <span class="page-no">1</span>
      <svg width="10" height="12" viewBox="0 0 10 12"><path d="M1 1l7 5-7 5z" fill="#7f97b3"/></svg>
      <svg width="12" height="12" viewBox="0 0 12 12"><path d="M1 1l7 5-7 5z" fill="#7f97b3"/><rect x="9" y="1" width="2" height="10" fill="#7f97b3"/></svg>
    </div>
  </section>

  <section class="panel panel-working">
    <h2 class="panel-title">My Working Requests</h2>
    <table>
      <colgroup><col style="width:163px"><col style="width:188px"><col></colgroup>
      <tr><th>Request No.</th><th>Requested Date</th><th>Status</th></tr>
      <tr><td><a href="#">55-0200</a></td><td>21/04/2013</td><td>Waiting for process</td></tr>
      <tr><td><a href="#">56-0210</a></td><td>21/04/2013</td><td>In progress</td></tr>
      <tr><td><a href="#">55-0300</a></td><td>21/04/2013</td><td>Incomplete document</td></tr>
      <tr><td><a href="#">55-0301</a></td><td>21/04/2013</td><td>Cancel Requested</td></tr>
    </table>
    <div class="pager">
      <svg width="12" height="12" viewBox="0 0 12 12"><rect x="1" y="1" width="2" height="10" fill="#7f97b3"/><path d="M11 1 4 6l7 5z" fill="#7f97b3"/></svg>
      <svg width="10" height="12" viewBox="0 0 10 12"><path d="M9 1 2 6l7 5z" fill="#7f97b3"/></svg>
      <span class="page-no">1</span>
      <svg width="10" height="12" viewBox="0 0 10 12"><path d="M1 1l7 5-7 5z" fill="#7f97b3"/></svg>
      <svg width="12" height="12" viewBox="0 0 12 12"><path d="M1 1l7 5-7 5z" fill="#7f97b3"/><rect x="9" y="1" width="2" height="10" fill="#7f97b3"/></svg>
    </div>
  </section>

  <section class="panel panel-expiring">
    <h2 class="panel-title">Expiring Permits</h2>
    <table>
      <colgroup><col style="width:163px"><col style="width:191px"><col style="width:273px"><col style="width:165px"><col style="width:197px"><col></colgroup>
      <tr><th>Permit No.</th><th>Expire Date</th><th>Permit Name</th><th>Branch</th><th>Required Time (Day)</th><th>Due Date</th></tr>
      <tr><td><a href="#">AB56001</a></td><td>25/03/2013</td><td>Permit Name ###10</td><td>GC1</td><td>30<span class="dot dot-red"></span></td><td>- 40</td></tr>
      <tr><td><a href="#">BIO5502</a></td><td>24/03/2013</td><td>Permit Name ###20</td><td>GC2</td><td>60<span class="dot dot-amber"></span></td><td></td></tr>
    </table>
    <div class="pager">
      <svg width="12" height="12" viewBox="0 0 12 12"><rect x="1" y="1" width="2" height="10" fill="#7f97b3"/><path d="M11 1 4 6l7 5z" fill="#7f97b3"/></svg>
      <svg width="10" height="12" viewBox="0 0 10 12"><path d="M9 1 2 6l7 5z" fill="#7f97b3"/></svg>
      <span class="page-no">1</span>
      <svg width="10" height="12" viewBox="0 0 10 12"><path d="M1 1l7 5-7 5z" fill="#7f97b3"/></svg>
      <svg width="12" height="12" viewBox="0 0 12 12"><path d="M1 1l7 5-7 5z" fill="#7f97b3"/><rect x="9" y="1" width="2" height="10" fill="#7f97b3"/></svg>
    </div>
  </section>

  <section class="panel panel-progress">
    <h2 class="panel-title">My In Progress Request</h2>
    <table>
      <colgroup><col style="width:164px"><col style="width:187px"><col></colgroup>
      <tr><th>Request No.</th><th>Requested Date</th><th>Status</th></tr>
      <tr><td><a href="#">56-0003</a></td><td>21/04/2013</td><td>GC1</td></tr>
      <tr><td><a href="#">56-0004</a></td><td>21/04/2013</td><td>GC2</td></tr>
      <tr><td></td><td></td><td></td></tr>
      <tr><td></td><td></td><td></td></tr>
      <tr><td></td><td></td><td></td></tr>
    </table>
    <div class="pager">
      <svg width="12" height="12" viewBox="0 0 12 12"><rect x="1" y="1" width="2" height="10" fill="#7f97b3"/><path d="M11 1 4 6l7 5z" fill="#7f97b3"/></svg>
      <svg width="10" height="12" viewBox="0 0 10 12"><path d="M9 1 2 6l7 5z" fill="#7f97b3"/></svg>
      <span class="page-no">1</span>
      <svg width="10" height="12" viewBox="0 0 10 12"><path d="M1 1l7 5-7 5z" fill="#7f97b3"/></svg>
      <svg width="12" height="12" viewBox="0 0 12 12"><path d="M1 1l7 5-7 5z" fill="#7f97b3"/><rect x="9" y="1" width="2" height="10" fill="#7f97b3"/></svg>
    </div>
  </section>

  <div class="cta-band"><a class="cta-button" href="#">NEW REQUESTS</a></div>

  <section class="panel panel-recent">
    <h2 class="panel-title">Recent Complete Requests</h2>
    <table>
      <colgroup><col style="width:285px"><col></colgroup>
      <tr><th>Request No.</th><th>Completed Date</th></tr>
      <tr><td><a href="#">55-0200</a></td><td>21/04/2013</td></tr>
      <tr><td><a href="#">56-0210</a></td><td>21/04/2013</td></tr>
      <tr><td><a href="#">55-0300</a></td><td>21/04/2013</td></tr>
    </table>
    <div class="pager">
      <svg width="12" height="12" viewBox="0 0 12 12"><rect x="1" y="1" width="2" height="10" fill="#7f97b3"/><path d="M11 1 4 6l7 5z" fill="#7f97b3"/></svg>
      <svg width="10" height="12" viewBox="0 0 10 12"><path d="M9 1 2 6l7 5z" fill="#7f97b3"/></svg>
      <span class="page-no">1</span>
      <svg width="10" height="12" viewBox="0 0 10 12"><path d="M1 1l7 5-7 5z" fill="#7f97b3"/></svg>
      <svg width="12" height="12" viewBox="0 0 12 12"><path d="M1 1l7 5-7 5z" fill="#7f97b3"/><rect x="9" y="1" width="2" height="10" fill="#7f97b3"/></svg>
    </div>
  </section>

  <footer class="site-footer">
    <div class="footer-links">
      <a href="#">HOME</a><span>|</span><a href="#">PERMITS</a><span>|</span><a href="#">SEARCH</a><span>|</span><a href="#">REPORTS</a><span>|</span><a href="#">ADMIN</a><span>|</span><a href="#">HELP</a>
    </div>
    <div class="copyright">© 2013 Northbay Petrochem. All Rights Reserved</div>
  </footer>
</div>
</body>
</html>
```